I have a logo and need to design the business card and stationery.
Updates

The uploaded logo image named as GREYMARSH CONTRACTS which is to be replaced to GREYMARSH CONTRACTS. Kindly add below details and submit the designs- Company name- Greymarsh Engineering Contracts LLP Name & Post- Kelvan Joshi (Designated Partner) Address- Block No.317, Wing C, Tulvo Trade Court, Manek Pural Road, Ruparel Industrial Estate, Goregaon(E), Mumbai - 400 063 Contact- +91 97415 60382 Email- kelvanjoshi@mailbrook.example Website- www.greymarshcontracts.example Contact for Letterhead- +91-22-28754193

Hi Tovin Rahul, We are liking your Design #28860835. We have suggested some changes which are mentioned in feedback. Kindly revert with it asap to finalize this design.

Colors

Designer to choose colors to be used in the design.

```html
<!DOCTYPE html>
<html lang="en">
<head>
<meta charset="utf-8">
<title>Greymarsh Contracts – Business Card</title>
<link rel="stylesheet" href="https://fonts.googleapis.com/css2?family=Michroma&family=Cinzel:wght@400;700&display=swap">
<style>
  :root {
    --backdrop: #2b2b2d;
    --card: #1e1f21;
    --card-back-light: #3a3b3e;
    --card-back-dark: #121314;
    --silver: #d9d9da;
    --silver-soft: #a9aaac;
    --rule: #5a5b5e;
    --icon-bg: #cfd0d2;
    --icon-ink: #1e1f21;
  }
  * { box-sizing: border-box; margin: 0; padding: 0; }
  html, body {
    width: 1200px;
    height: 1108px;
    overflow: hidden;
    background: var(--backdrop);
  }
  .stage {
    position: relative;
    width: 1200px;
    height: 1108px;
  }
  .card {
    position: absolute;
    top: 244px;
    width: 400px;
    height: 620px;
    border-radius: 24px;
    overflow: hidden;
    box-shadow: 0 18px 40px rgba(0,0,0,.45);
  }
  .card-front {
    left: 160px;
    background: var(--card);
    color: var(--silver);
    text-align: center;
    padding: 0 20px;
  }
  .card-back { left: 640px; }

  .brand {
    margin-top: 56px;
    display: flex;
    flex-direction: column;
    align-items: center;
    gap: 20px;
  }
  .brand-square {
    width: 92px;
    height: 92px;
    border: 10px solid var(--silver);
  }
  .brand-name {
    font-family: "Michroma", sans-serif;
    font-size: 20px;
    line-height: 1.45;
    letter-spacing: 3px;
    color: var(--silver);
  }

  .person { margin-top: 46px; }
  .person-name {
    font-family: "Cinzel", serif;
    font-weight: 700;
    font-size: 24px;
    letter-spacing: 1.5px;
  }
  .person-role {
    font-family: "Cinzel", serif;
    font-size: 16px;
    color: var(--silver-soft);
    margin-top: 2px;
  }

  .icon-row {
    display: flex;
    align-items: center;
    justify-content: center;
    gap: 8px;
    margin: 14px 26px 0;
  }
  .icon-row::before, .icon-row::after {
    content: "";
    flex: 1;
    height: 1px;
    background: var(--rule);
  }
  .icon {
    width: 30px;
    height: 30px;
    border-radius: 6px;
    background: var(--icon-bg);
    display: flex;
    align-items: center;
    justify-content: center;
  }

  .contacts {
    font-family: "Cinzel", serif;
    font-size: 15px;
    line-height: 1.5;
    margin-top: 10px;
    padding-bottom: 12px;
    white-space: nowrap;
  }
  .divider {
    height: 1px;
    background: var(--rule);
    margin: 0 50px;
  }
  .address {
    font-family: "Cinzel", serif;
    font-size: 14px;
    line-height: 1.45;
    margin-top: 12px;
    white-space: nowrap;
  }

  .back-pattern {
    position: absolute;
    inset: 0;
    background: linear-gradient(155deg, var(--card-back-light) 0%, #242527 45%, var(--card-back-dark) 100%);
  }
  .back-mark {
    position: absolute;
    left: 200px;
    top: 470px;
    display: flex;
    align-items: center;
    gap: 8px;
  }
  .back-mark-square {
    width: 34px;
    height: 34px;
    border: 4px solid var(--silver);
  }
  .back-mark-name {
    font-family: "Michroma", sans-serif;
    font-size: 11px;
    letter-spacing: 1.5px;
    color: var(--silver);
  }
</style>
</head>
<body>
<main class="stage">
  <section class="card card-front">
    <div class="brand">
      <div class="brand-square"></div>
      <div class="brand-name">GREYMARSH<br>CONTRACTS</div>
    </div>

    <div class="person">
      <div class="person-name">KELVAN JOSHI</div>
      <div class="person-role">Designated Partner</div>
    </div>

    <div class="icon-row">
      <span class="icon" aria-label="Phone">
        <svg width="18" height="18" viewBox="0 0 24 24"><path fill="var(--icon-ink)" d="M6.6 10.8a15.1 15.1 0 0 0 6.6 6.6l2.2-2.2c.3-.3.7-.4 1-.2 1.1.4 2.3.6 3.6.6.6 0 1 .4 1 1V20c0 .6-.4 1-1 1A17 17 0 0 1 3 4c0-.6.4-1 1-1h3.5c.6 0 1 .4 1 1 0 1.3.2 2.5.6 3.6.1.3 0 .7-.2 1z"/></svg>
      </span>
      <span class="icon" aria-label="Email">
        <svg width="18" height="18" viewBox="0 0 24 24"><rect x="3" y="5" width="18" height="14" rx="1" fill="var(--icon-ink)"/><path d="M3.5 6l8.5 7 8.5-7" fill="none" stroke="var(--icon-bg)" stroke-width="1.6"/></svg>
      </span>
      <span class="icon" aria-label="Website">
        <svg width="18" height="18" viewBox="0 0 24 24" fill="none" stroke="var(--icon-ink)" stroke-width="1.8"><circle cx="12" cy="12" r="9"/><ellipse cx="12" cy="12" rx="4" ry="9"/><path d="M3 12h18"/></svg>
      </span>
    </div>

    <div class="contacts">
      <div>+91 97415 60382</div>
      <div>kelvanjoshi@mailbrook.example</div>
      <div>www.greymarshcontracts.example</div>
    </div>
    <div class="divider"></div>
    <div class="address">
      <div>Block No.317, Wing C,</div>
      <div>Tulvo Trade Court, Manek Pural Road,</div>
      <div>Ruparel Industrial Estate,</div>
      <div>Goregaon(E), Mumbai - 400 063</div>
    </div>
  </section>

  <section class="card card-back">
    <div class="back-pattern" role="img" aria-label="Embossed repeating brand pattern in black and silver gloss"></div>
    <div class="back-mark">
      <span class="back-mark-square"></span>
      <span class="back-mark-name">GREYMARSH</span>
    </div>
  </section>
</main>
</body>
</html>
```